Flyer-Design für Kindertagesstätte
Felmriks Spielhafen suchte ein neues Design in der Kategorie Flyer und hat ein Projekt auf grafikwunsch.de gestartet.
Zielgruppe
Wir sind eine Kindertagesstätte und wollen eine Baby-Kind-Spielgruppe jeden Mittwoch in unserer Kita von 09.00 Uhr bis 11.00 Uhr anbieten.
Aufgabenstellung
Unser LOGO muss im Flyer enthalten sein, auf jeden Fall ein Bild wenn möglich mit mehreren Babys/Kleinkindern bis 1,5 Jahre. Wir benötigen den Flyer in DIN lang - bunt - 1 seitig.
Folgender Text sollte enthalten: Baby-Kind-Spielgruppe, jeden mittwoch in unserer Kita 'Felmriks Spielhafen' von 09.00 Uhr bis 11.00 Uhr. Die Spielgruppe wird durch unser ausgebildetes Fachpersonal begleitet.

```html
<!DOCTYPE html>
<html lang="de">
<head>
<meta charset="utf-8">
<title>Baby-Kind Spielgruppe – Felmriks Spielhafen</title>
<link href="https://fonts.googleapis.com/css2?family=Amatic+SC:wght@700&family=Open+Sans:wght@400;700&display=swap" rel="stylesheet">
<style>
  :root {
    --teal: #45a3b9;
    --teal-light: #7cc6d6;
    --pink: #e9546b;
    --cream: #fbf1e2;
    --white: #ffffff;
    --ink: #3a3a3a;
  }
  html, body { margin: 0; padding: 0; overflow: hidden; background: #ffffff; }
  .flyer {
    position: relative; width: 1200px; height: 600px; overflow: hidden;
    font-family: "Open Sans", Arial, sans-serif; color: var(--ink);
  }
  .band { position: absolute; left: 0; width: 1200px; }
  .band-top { top: 0; height: 300px; background: var(--teal); }
  .band-contact { top: 300px; height: 123px; background: var(--pink); }
  .band-note { top: 423px; height: 87px; background: var(--cream); }
  .band-blocks {
    top: 510px; height: 90px;
    background: linear-gradient(90deg, #d8453c 0%, #f08a3a 22%, #8fc35a 40%, #b58ad0 55%, #5fb4e0 72%, #f0d84a 90%, #e3e070 100%);
  }
  .zigzag { position: absolute; left: 0; top: 294px; }
  .title {
    position: absolute; left: 36px; top: 14px; margin: 0;
    font-family: "Amatic SC", "Comic Sans MS", cursive;
    font-weight: 700; font-size: 76px; letter-spacing: 7px; line-height: 1;
    color: var(--white); text-transform: uppercase;
  }
  .schedule {
    position: absolute; left: 34px; top: 108px; width: 455px; height: 127px;
    box-sizing: border-box; padding: 20px 0 0 26px;
    background: var(--cream); border: 3px dotted var(--teal-light);
    outline: 3px solid var(--cream); font-size: 19.5px; line-height: 27px;
  }
  .schedule p { margin: 0; }
  .accent { color: var(--pink); font-weight: 700; }
  .photo {
    position: absolute; box-sizing: border-box; border: 8px solid var(--cream);
  }
  .photo-baby {
    left: 532px; top: 111px; width: 270px; height: 262px;
    border-radius: 18px 110px 18px 110px;
    background: linear-gradient(160deg, #eceaea 0%, #e6d3c8 45%, #d9c4b8 70%, #c9c2c4 100%);
  }
  .photo-play {
    left: 821px; top: 34px; width: 345px; height: 334px;
    border-radius: 130px 18px 130px 18px;
    background: linear-gradient(150deg, #d9b784 0%, #cfd6dc 35%, #e6cfc2 60%, #8fb07a 85%, #e58a48 100%);
  }
  .badge {
    position: absolute; left: 736px; top: 293px; width: 150px; height: 150px;
    box-sizing: border-box; border-radius: 50%;
    background: var(--white); border: 8px solid var(--teal-light);
    display: flex; flex-direction: column; align-items: center; justify-content: center; gap: 8px;
  }
  .badge-dot { width: 26px; height: 26px; border-radius: 50%; background: var(--pink); }
  .badge-name {
    font-size: 13px; font-weight: 700; color: var(--pink); text-align: center; line-height: 1.2;
  }
  .contact {
    position: absolute; left: 37px; top: 328px; margin: 0;
    color: var(--white); font-size: 19.5px; line-height: 29px;
  }
  .contact strong { font-weight: 700; }
  .note {
    position: absolute; left: 34px; top: 438px; margin: 0;
    font-size: 19.5px; line-height: 27px; color: var(--ink);
  }
</style>
</head>
<body>
<main class="flyer">
  <div class="band band-top"></div>
  <div class="band band-contact"></div>
  <div class="band band-note"></div>
  <div class="band band-blocks" role="img" aria-label="Foto bunter Schaumstoff-Bauklötze"></div>

  <svg class="zigzag" width="1200" height="8" viewBox="0 0 1200 8" aria-hidden="true">
    <defs>
      <pattern id="zig" width="10" height="8" patternUnits="userSpaceOnUse">
        <polyline points="0,7 5,1 10,7" fill="none" stroke="#fbf1e2" stroke-width="1.6"/>
      </pattern>
    </defs>
    <rect width="1200" height="8" fill="url(#zig)"/>
  </svg>

  <h1 class="title">Baby-Kind Spielgruppe</h1>

  <section class="schedule">
    <p class="accent">jeden Mittwoch</p>
    <p>in unserer Kita „Felmriks Spielhafen“</p>
    <p class="accent">von 09.00 Uhr bis 11.00 Uhr</p>
  </section>

  <div class="photo photo-baby" role="img" aria-label="Foto eines Babys, das auf einer Decke sitzt und mit einem Spielzeug spielt"></div>
  <div class="photo photo-play" role="img" aria-label="Foto von zwei Kleinkindern, die mit bunten Stapelringen spielen"></div>

  <div class="badge">
    <span class="badge-dot"></span>
    <span class="badge-name">Felmriks<br>Spielhafen</span>
  </div>

  <p class="contact">
    Voranmeldungen bitte telefonisch unter:<br>
    <strong>0351 / 48 27 615</strong> oder unter<br>
    <strong>www.felmriks-spielhafen.de</strong>
  </p>

  <p class="note">
    Die Spielgruppe wird durch unser ausgebildetes Fachpersonal begleitet.<br>
    Spielgruppe ist öffentlich und kostenfrei.
  </p>
</main>
</body>
</html>
```